Business card for law firm

Need business card for new law firm. Think confident, authoritative, conservative, but not stuffy or old-fashioned.

Contact Information for Business Card

Content for card - logo (uploaded), plus the following:

Paul Whitcombe (larger font)
Managing Partner (larger font, but not as large as name)
Level 9, 7 Ferris Lane
Sydney NSW 2000
Main Tel 02 9364 2710
Direct Tel 02 8472 3159
Email paul@qvlegal.com.au
www.qvlegal.com.au

Letterhead design should include logo plus:
Level 9, 7 Ferris Lane
Sydney NSW 2000
Tel 02 8472 3159
www.qvlegal.com.au

```html
<!DOCTYPE html>
<html lang="en">
<head>
<meta charset="utf-8">
<title>Quayvale Legal – Business Card</title>
<link rel="stylesheet" href="https://fonts.googleapis.com/css2?family=Open+Sans:wght@400;600;700&display=swap">
<style>
  :root {
    --navy: #0d1f5c;
    --ink: #111111;
    --text-grey: #333333;
    --paper: #ffffff;
    --backdrop: #e6e7ea;
    --card-shadow: rgba(0, 0, 0, 0.12);
  }
  * { box-sizing: border-box; margin: 0; padding: 0; }
  html, body {
    width: 1200px;
    height: 960px;
    overflow: hidden;
  }
  body {
    background: var(--backdrop);
    font-family: "Open Sans", Arial, sans-serif;
    color: var(--ink);
    position: relative;
  }
  .card {
    position: absolute;
    left: 250px;
    width: 700px;
    height: 428px;
    background: var(--paper);
    box-shadow: 0 6px 20px var(--card-shadow);
    overflow: hidden;
  }
  .card--front { top: 40px; }
  .card--back { top: 492px; }

  /* Brand lockup */
  .brand {
    display: flex;
    flex-direction: column;
    align-items: center;
  }
  .brand__mark {
    width: 46px;
    height: 46px;
    background: var(--navy);
    margin-bottom: 14px;
  }
  .brand__name {
    font-size: 34px;
    font-weight: 400;
    letter-spacing: 0.12em;
    color: var(--ink);
    text-transform: uppercase;
    white-space: nowrap;
  }

  /* Front */
  .card--front .brand {
    position: absolute;
    top: 120px;
    left: 0;
    right: 0;
  }
  .front__web {
    margin-top: 18px;
    font-size: 15px;
    letter-spacing: 0.22em;
    color: var(--text-grey);
  }

  /* Back */
  .card--back .brand {
    position: absolute;
    top: 34px;
    left: 56px;
  }
  .card--back .brand__mark { width: 40px; height: 40px; margin-bottom: 10px; }
  .card--back .brand__name { font-size: 28px; }

  .address {
    position: absolute;
    top: 148px;
    left: 56px;
    font-size: 16px;
    line-height: 1.4;
    color: var(--text-grey);
  }
  .person {
    position: absolute;
    top: 150px;
    right: 40px;
    text-align: right;
  }
  .person__name {
    font-size: 21px;
    font-weight: 700;
    color: var(--navy);
    letter-spacing: 0.01em;
  }
  .person__title {
    font-size: 14px;
    color: var(--text-grey);
    letter-spacing: 0.03em;
    margin-top: 2px;
  }

  .wave {
    position: absolute;
    left: 0;
    bottom: 0;
    width: 700px;
    height: 428px;
  }
  .wave__navy { fill: var(--navy); }
  .wave__swoosh { fill: var(--ink); }

  .contacts {
    position: absolute;
    right: 24px;
    top: 326px;
    list-style: none;
    color: var(--paper);
    font-size: 15px;
    line-height: 22px;
  }
  .contacts__item {
    display: flex;
    justify-content: flex-end;
    align-items: center;
    gap: 8px;
  }
  .contacts__icon {
    width: 14px;
    height: 14px;
    flex: none;
  }
</style>
</head>
<body>

  <section class="card card--front" aria-label="Business card front">
    <div class="brand">
      <div class="brand__mark"></div>
      <div class="brand__name">Quayvale Legal</div>
      <div class="front__web">www.qvlegal.com.au</div>
    </div>
  </section>

  <section class="card card--back" aria-label="Business card back">
    <svg class="wave" viewBox="0 0 700 428" aria-hidden="true">
      <path class="wave__swoosh" d="M0,196 C140,246 300,296 460,302 C580,306 650,292 700,282 L700,290 C640,304 560,316 460,316 C300,312 140,264 0,220 Z"/>
      <path class="wave__navy" d="M0,232 C130,282 290,330 450,332 C570,333 640,314 700,300 L700,428 L0,428 Z"/>
    </svg>

    <div class="brand">
      <div class="brand__mark"></div>
      <div class="brand__name">Quayvale Legal</div>
    </div>

    <address class="address" style="font-style: normal;">
      Level 9, 7 Ferris Lane<br>
      Sydney NSW 2000
    </address>

    <div class="person">
      <div class="person__name">PAUL WHITCOMBE</div>
      <div class="person__title">MANAGING PARTNER</div>
    </div>

    <ul class="contacts">
      <li class="contacts__item">02 9364 2710 (Main)
        <svg class="contacts__icon" viewBox="0 0 14 14" aria-hidden="true"><circle cx="7" cy="7" r="7" fill="#fff"/><path d="M4.5 3.5 L6 3.5 L6.5 5.5 L5.6 6.2 C6.1 7.3 6.8 8 7.8 8.4 L8.5 7.5 L10.5 8 L10.5 9.5 C7 10 4 7 4.5 3.5 Z" fill="#0d1f5c"/></svg>
      </li>
      <li class="contacts__item">02 8472 3159 (Direct)
        <svg class="contacts__icon" viewBox="0 0 14 14" aria-hidden="true"><circle cx="7" cy="7" r="7" fill="#fff"/><path d="M4.5 3.5 L6 3.5 L6.5 5.5 L5.6 6.2 C6.1 7.3 6.8 8 7.8 8.4 L8.5 7.5 L10.5 8 L10.5 9.5 C7 10 4 7 4.5 3.5 Z" fill="#0d1f5c"/></svg>
      </li>
      <li class="contacts__item">paul@qvlegal.com.au
        <svg class="contacts__icon" viewBox="0 0 14 14" aria-hidden="true"><circle cx="7" cy="7" r="7" fill="#fff"/><rect x="3.5" y="4.5" width="7" height="5" fill="#0d1f5c"/><path d="M3.5 4.5 L7 7.3 L10.5 4.5" fill="none" stroke="#fff" stroke-width="0.8"/></svg>
      </li>
      <li class="contacts__item">www.qvlegal.com.au
        <svg class="contacts__icon" viewBox="0 0 14 14" aria-hidden="true"><circle cx="7" cy="7" r="7" fill="#fff"/><circle cx="7" cy="7" r="4" fill="none" stroke="#0d1f5c" stroke-width="1"/><ellipse cx="7" cy="7" rx="1.8" ry="4" fill="none" stroke="#0d1f5c" stroke-width="0.8"/><path d="M3 7 H11" stroke="#0d1f5c" stroke-width="0.8"/></svg>
      </li>
    </ul>
  </section>

</body>
</html>
```